Business Card Design

New business card design

Target Market(s)

Residential & Commercial Property Managers

Industry/Entity Type

Plumbing Services

Contact Information for Business Card

Name - Rowan Keddle, title - Director, Phone Number - 0431 286 517, email - rowan@tbk-plumbing.com.au, Company ABN - 73 215 904 386,

Font styles to use
Sans Serif

Colors
0054AA
0677BA
7BADD7
CADEEF
E8F1F8

```html
<!DOCTYPE html>
<html lang="en">
<head>
<meta charset="utf-8">
<title>TBK Plumbing Services – Business Card</title>
<link href="https://fonts.googleapis.com/css2?family=Montserrat:wght@400;500;700&display=swap" rel="stylesheet">
<style>
  :root {
    --page-bg: #d3d8d8;
    --card-white: #f1f1ef;
    --brand-blue: #41bdee;
    --brand-blue-deep: #0677ba;
    --ink: #1d2326;
    --ink-soft: #3a4246;
    --paper-edge: #ffffff;
  }
  * { box-sizing: border-box; margin: 0; padding: 0; }
  html, body {
    width: 1200px; height: 881px; overflow: hidden;
    background: var(--page-bg);
    font-family: "Montserrat", sans-serif;
  }
  .sheet {
    position: relative; width: 1200px; height: 881px;
    display: flex; align-items: center; justify-content: center; gap: 40px;
  }
  .card {
    position: relative; width: 540px; height: 309px;
    box-shadow: 0 14px 30px rgba(0,0,0,0.18);
  }
  .card--front {
    background: var(--card-white);
    border-bottom: 3px solid var(--brand-blue);
  }
  .card--back { background: var(--brand-blue); }

  .wordmark {
    position: absolute; display: flex; align-items: center; gap: 10px;
    font-weight: 500; white-space: nowrap;
  }
  .wordmark__dot {
    width: 12px; height: 12px; border-radius: 50%;
    background: var(--brand-blue);
  }
  .card--front .wordmark {
    top: 34px; left: 150px; font-size: 26px; color: var(--ink);
    letter-spacing: 0.5px;
  }
  .card--back .wordmark {
    top: 50%; left: 50%; transform: translate(-50%, -50%);
    font-size: 36px; color: var(--paper-edge); letter-spacing: 1px;
  }
  .card--back .wordmark__dot { background: var(--paper-edge); width: 16px; height: 16px; }

  .abn {
    position: absolute; top: 104px; left: 80px;
    font-size: 13px; color: var(--ink-soft);
  }
  .contact {
    position: absolute; left: 34px; bottom: 56px;
    list-style: none; font-size: 13px; color: var(--ink-soft);
  }
  .contact__item { display: flex; align-items: center; gap: 8px; line-height: 20px; }
  .contact__icon { width: 11px; height: 11px; flex: none; }

  .person {
    position: absolute; right: 34px; top: 196px; text-align: right;
  }
  .person__name {
    font-weight: 700; font-size: 18px; color: var(--brand-blue);
  }
  .person__title {
    font-size: 13px; color: var(--ink-soft); margin-top: 4px;
  }
  .accent-bar {
    position: absolute; right: 0; top: 196px;
    width: 18px; height: 46px; background: var(--brand-blue);
  }
</style>
</head>
<body>
<main class="sheet">
  <section class="card card--front" aria-label="Business card front">
    <div class="wordmark">
      <span class="wordmark__text">TBK Plumbing Services</span>
      <span class="wordmark__dot"></span>
    </div>
    <p class="abn">Company ABN - 73 215 904 386</p>
    <ul class="contact">
      <li class="contact__item">
        <svg class="contact__icon" viewBox="0 0 24 24" aria-hidden="true">
          <path fill="#41bdee" d="M6.6 10.8a15.1 15.1 0 0 0 6.6 6.6l2.2-2.2c.3-.3.7-.4 1-.2 1.1.4 2.3.6 3.6.6.6 0 1 .4 1 1V20c0 .6-.4 1-1 1C10.6 21 3 13.4 3 4c0-.6.4-1 1-1h3.5c.6 0 1 .4 1 1 0 1.3.2 2.5.6 3.6.1.3 0 .7-.2 1z"/>
        </svg>
        <span>0431 286 517</span>
      </li>
      <li class="contact__item">
        <svg class="contact__icon" viewBox="0 0 24 24" aria-hidden="true">
          <rect x="2" y="5" width="20" height="14" rx="2" fill="#41bdee"/>
          <path d="M3 6l9 7 9-7" fill="none" stroke="#ffffff" stroke-width="1.8"/>
        </svg>
        <span>rowan@tbk-plumbing.com.au</span>
      </li>
    </ul>
    <div class="person">
      <p class="person__name">Rowan Keddle</p>
      <p class="person__title">Director</p>
    </div>
    <div class="accent-bar"></div>
  </section>

  <section class="card card--back" aria-label="Business card back">
    <div class="wordmark">
      <span class="wordmark__text">TBK Plumbing Services</span>
      <span class="wordmark__dot"></span>
    </div>
  </section>
</main>
</body>
</html>
```